Redesign of business card for Cedar Ridge Mechanical

We are looking for a new design for our business cards for Cedar Ridge Mechanical. We are a plumbing & HVAC construction company, operating on the West Coast of Canada and USA. Logo attached.
Industry/Entity Type
Construction - Plumbing & HVAC
Contact Information for Business Card
Name, address, phone numbers, email, website address
Look and feel
Each slider illustrates characteristics of the customer's brand and the style your logo design should communicate.

```html
<!DOCTYPE html>
<html lang="en">
<head>
<meta charset="utf-8">
<title>Cedar Ridge Mechanical – Business Card</title>
<link href="https://fonts.googleapis.com/css2?family=Montserrat:wght@400;500;700;800&display=swap" rel="stylesheet">
<style>
  :root {
    --stage: #1a1a1a;
    --card: #161616;
    --ink: #ffffff;
    --soft: #d9d9d9;
    --rule: #8a8a8a;
    --swoosh-edge: #5a5a5a;
  }
  * { margin: 0; padding: 0; box-sizing: border-box; }
  html, body { width: 1200px; height: 963px; overflow: hidden; background: var(--stage); }
  body { font-family: "Montserrat", sans-serif; color: var(--ink); }

  .business-card {
    position: absolute;
    left: 160px; top: 230px;
    width: 880px; height: 503px;
    border-radius: 30px;
    overflow: hidden;
    background: var(--card);
    box-shadow: 0 20px 50px rgba(0,0,0,.6);
  }
  .card-base { position: absolute; inset: 0; }

  .brand {
    position: absolute;
    left: 360px; top: 70px;
    display: flex; align-items: center; gap: 18px;
  }
  .brand-square {
    width: 54px; height: 54px;
    border: 6px solid var(--ink);
    border-radius: 6px;
  }
  .brand-name {
    font-weight: 700;
    font-size: 30px;
    letter-spacing: 1px;
    line-height: 1.15;
    text-transform: uppercase;
  }

  .identity {
    position: absolute;
    right: 490px; top: 232px;
    text-align: right;
  }
  .person-name { font-weight: 800; font-size: 27px; letter-spacing: .5px; }
  .person-role { font-weight: 400; font-size: 20px; color: var(--soft); margin-top: 2px; }

  .divider {
    position: absolute;
    left: 410px; top: 232px;
    width: 1.5px; height: 96px;
    background: var(--rule);
  }

  .contacts {
    position: absolute;
    left: 428px; top: 236px;
    list-style: none;
    font-size: 24px; font-weight: 400;
    line-height: 32px;
  }
  .contacts li { display: flex; align-items: center; gap: 10px; white-space: nowrap; }
  .contacts svg { width: 18px; height: 18px; flex: none; fill: var(--ink); }

  .address {
    position: absolute;
    left: 120px; top: 338px;
    font-size: 24px; font-weight: 400;
    white-space: nowrap;
  }
</style>
</head>
<body>
  <article class="business-card">
    <svg class="card-base" viewBox="0 0 880 503" aria-hidden="true">
      <path d="M0,455 Q440,470 880,405" fill="none" stroke="var(--swoosh-edge)" stroke-width="6"/>
      <path d="M0,465 Q440,478 880,418 L880,503 L0,503 Z" fill="var(--ink)"/>
    </svg>

    <div class="brand">
      <span class="brand-square"></span>
      <span class="brand-name">Cedar Ridge<br>Mechanical</span>
    </div>

    <div class="identity">
      <p class="person-name">MARCUS HALE</p>
      <p class="person-role">Manager</p>
    </div>

    <span class="divider"></span>

    <ul class="contacts">
      <li>
        <svg viewBox="0 0 24 24"><path d="M6.6 10.8a15 15 0 0 0 6.6 6.6l2.2-2.2c.3-.3.7-.4 1-.2 1.1.4 2.3.6 3.6.6.6 0 1 .4 1 1V20c0 .6-.4 1-1 1A17 17 0 0 1 3 4c0-.6.4-1 1-1h3.5c.6 0 1 .4 1 1 0 1.3.2 2.5.6 3.6.1.3 0 .7-.2 1z"/></svg>
        604-555-0182
      </li>
      <li>
        <svg viewBox="0 0 24 24"><path d="M2 5h20v14H2z M4 7v.5l8 5 8-5V7z" fill-rule="evenodd"/></svg>
        info@cedarridgemech.com
      </li>
      <li>
        <svg viewBox="0 0 24 24"><circle cx="12" cy="12" r="10"/></svg>
        www.cedarridgemech.com
      </li>
    </ul>

    <p class="address">2150 Harbour Rd, Vancouver, BC V6B 0A1</p>
  </article>
</body>
</html>
```